"The Plumewright" nails, eyelash extensions and hair extensions. Need an eye catching design for bu

Need an eye catching design focusing on eyelash extensions, nail extensions and hair extensions. I like the colour green, black, glitter, pink?! need the design to be innovative and 'POP'. I'd like more emphasis on lashes and nails.
I'd like the business name and my phone number on the front of card.
Would really like something different and unique.
"The Plumewright"
Nails, Eyelash & Hair Extensions
Mira
0471526093

Target Market(s)

20-40

Industry/Entity Type

Beauty Salon

Contact Information for Business Card

Id like my business name, My name and phone number on the front of card
"The Plumewright".
Mira.
0471526093.
Id like some catchy design involving long lashes with possibly glitter, long hair and nails. Id like the lashes to be the first thing you see at first glance. I'm open to your creative flair. Just need the business card design to 'POP'! I like the colours green, black, pink, silver or gold glitter. wether it's pop art, 3d drawn pictures, isolated pics of lash, nails or hair, card design could be in black and white with isolated colours added..i'm open to your creative flair. use a font which stands out and easy to read.
(The back of the card will be used for writing appointment times.)

Font styles to use
Serif

Colors
6b449b
e667a6
25b39d

Requirements
Must have
• Long lashes, hair, nails.
• one sided
Nice to have
• bright catchy colours, innovative, uniqueness

```html
<!DOCTYPE html>
<html lang="en">
<head>
<meta charset="utf-8">
<title>The Plumewright – Appointment Cards</title>
<link rel="stylesheet" href="https://fonts.googleapis.com/css2?family=Cormorant+Garamond:ital,wght@0,600;1,700&family=Open+Sans:wght@400;600&display=swap">
<style>
  :root {
    --canvas: #e9e4de;
    --card-rim: #4a4a4a;
    --ink: #0b0b0b;
    --green-deep: #0c1a15;
    --green-glow: #1f3a31;
    --gold: #d9c07a;
    --gold-soft: rgba(217, 192, 122, 0.55);
    --photo-light: #9a9a9a;
    --photo-dark: #1a1a1a;
    --panel: rgba(200, 200, 200, 0.28);
  }
  * { box-sizing: border-box; margin: 0; padding: 0; }
  html, body { width: 1200px; height: 800px; overflow: hidden; }
  body {
    background: var(--canvas);
    position: relative;
    font-family: "Open Sans", sans-serif;
  }
  .card {
    position: absolute;
    top: 140px;
    width: 520px;
    height: 520px;
    border-radius: 22px;
    border: 8px solid var(--card-rim);
    overflow: hidden;
  }
  .card--front { left: 50px; background: var(--ink); }
  .card--back {
    left: 630px;
    background: radial-gradient(circle at 50% 42%, var(--green-glow) 0%, var(--green-deep) 70%);
  }
  .frame {
    position: absolute;
    inset: 22px;
    border: 1.5px solid var(--gold);
    pointer-events: none;
  }
  .corner {
    position: absolute;
    width: 54px;
    height: 54px;
    background: var(--gold-soft);
    border-radius: 4px;
  }
  .corner--tl { top: 14px; left: 14px; }
  .corner--tr { top: 14px; right: 14px; }
  .corner--bl { bottom: 14px; left: 14px; }
  .corner--br { bottom: 14px; right: 14px; }

  .portrait {
    position: absolute;
    left: 30px; right: 30px; top: 120px; bottom: 30px;
    background: radial-gradient(ellipse at 55% 45%, var(--photo-light) 0%, #555 40%, var(--photo-dark) 80%);
  }
  .contact {
    position: absolute;
    top: 40px; right: 110px;
    color: var(--gold);
    font-size: 15px;
    letter-spacing: 1px;
  }
  .business-name {
    position: absolute;
    top: 54px; left: 70px;
    color: var(--gold);
    font-family: "Cormorant Garamond", serif;
    font-style: italic;
    font-weight: 700;
    font-size: 50px;
    line-height: 1;
  }
  .owner-name {
    position: absolute;
    top: 108px; right: 60px;
    color: var(--gold);
    font-family: "Cormorant Garamond", serif;
    font-style: italic;
    font-weight: 700;
    font-size: 34px;
  }
  .services {
    position: absolute;
    top: 110px; left: 72px;
    color: var(--gold);
    font-family: "Cormorant Garamond", serif;
    font-weight: 600;
    font-size: 18px;
  }
  .appointment {
    position: absolute;
    left: 60px; top: 200px;
    width: 230px; height: 170px;
    background: var(--panel);
    border-radius: 16px;
    padding: 18px 18px 0;
  }
  .appointment__row {
    display: flex;
    align-items: flex-end;
    gap: 10px;
    height: 42px;
    color: #f1f1f1;
    font-size: 12px;
    letter-spacing: 1px;
  }
  .appointment__line { flex: 1; border-bottom: 1px solid var(--gold-soft); height: 1px; margin-bottom: 4px; }
  .appointment__label { width: 42px; }
  .next-label {
    position: absolute;
    left: 64px; top: 380px;
    color: #e6e6e6;
    font-size: 13px;
    letter-spacing: 1px;
  }

  .seal {
    position: absolute;
    left: 50%; top: 50%;
    width: 230px; height: 230px;
    margin: -125px 0 0 -115px;
    border: 3px solid var(--gold);
    border-radius: 50%;
    display: flex;
    align-items: center;
    justify-content: center;
  }
  .seal__name {
    color: var(--gold);
    font-family: "Cormorant Garamond", serif;
    font-weight: 600;
    font-size: 32px;
  }
</style>
</head>
<body>
  <section class="card card--front">
    <div class="portrait" role="img" aria-label="Black and white photograph of a woman with long lashes and nails holding a vintage telephone"></div>
    <div class="frame"></div>
    <div class="corner corner--tl" role="img" aria-label="Gold filigree corner ornament"></div>
    <div class="corner corner--tr" role="img" aria-label="Gold filigree corner ornament"></div>
    <div class="corner corner--bl" role="img" aria-label="Gold filigree corner ornament"></div>
    <div class="corner corner--br" role="img" aria-label="Gold filigree corner ornament"></div>
    <p class="contact">M: 0471526093</p>
    <h1 class="business-name">The Plumewright</h1>
    <p class="services">Nails | Hair Extensions | Eyelash</p>
    <p class="owner-name">Mira</p>
    <div class="appointment">
      <div class="appointment__row"><span class="appointment__label">NAME</span><span class="appointment__line"></span></div>
      <div class="appointment__row"><span class="appointment__label">TIME</span><span class="appointment__line"></span></div>
      <div class="appointment__row"><span class="appointment__label">DATE</span><span class="appointment__line"></span></div>
    </div>
    <p class="next-label">next appointment</p>
  </section>

  <section class="card card--back">
    <div class="frame"></div>
    <div class="corner corner--tl" role="img" aria-label="Gold filigree corner ornament"></div>
    <div class="corner corner--tr" role="img" aria-label="Gold filigree corner ornament"></div>
    <div class="corner corner--bl" role="img" aria-label="Gold filigree corner ornament"></div>
    <div class="corner corner--br" role="img" aria-label="Gold filigree corner ornament"></div>
    <div class="seal"><span class="seal__name">The Plumewright</span></div>
  </section>
</body>
</html>
```